Marlowe Crest Realty business card design

Looking for an upscale and clean business card design and updated logo. I sell to a very high-end south Florida real estate market.
Target Market(s)
High-end real estate in south Florida real estate market
Industry/Entity Type
Real Estate Agent
Contact Information for Business Card
Marlowe Crest Realty, Inc
738 West Pinecrest Ave, Suite 410/510, Fort Lauderdale, FL 33308
Gary Whitlock - Broker/Owner
954-327-8846 Direct
garyshomes@quellmail.com
Website: DwellTarrowBay.com
Font styles to use
Other font styles liked:
- Copperplate Gothic, Georgia, etc.
Requirements
Must have
- My photo, company name, my name and title, all info stated in Details above
Nice to have
- Luxury home design element, waterfront

```html
<!DOCTYPE html>
<html lang="en">
<head>
<meta charset="utf-8">
<title>Marlowe Crest Realty – Business Card</title>
<link rel="stylesheet" href="https://fonts.googleapis.com/css2?family=Montserrat:wght@700&family=Arimo:wght@400&display=swap">
<style>
  :root {
    --stage: #e9e9ea;
    --card-white: #ffffff;
    --card-black: #2f2f31;
    --back-mark: #4a4a4d;
    --gold: #f4c430;
    --ink: #3b3b3b;
    --ink-soft: #555555;
    --rule: #5a5a5a;
    --photo-a: #cfd6de;
    --photo-b: #2f4f9a;
  }
  * { box-sizing: border-box; margin: 0; padding: 0; }
  html, body { width: 1200px; height: 900px; overflow: hidden; }
  body {
    background: var(--stage);
    position: relative;
    font-family: "Arimo", Arial, sans-serif;
  }
  .card {
    position: absolute;
    left: 250px;
    width: 700px;
    height: 400px;
    border-radius: 28px;
    overflow: hidden;
  }
  /* Back side */
  .card-back {
    top: 35px;
    background: var(--card-black);
    display: flex;
    align-items: center;
    justify-content: center;
    gap: 22px;
  }
  .card-back .brand-dot {
    width: 74px; height: 74px;
    border-radius: 50%;
    background: var(--back-mark);
  }
  .card-back .brand-name {
    color: var(--back-mark);
    font-size: 40px;
    letter-spacing: 1px;
  }
  /* Front side */
  .card-front {
    top: 465px;
    background: var(--card-white);
  }
  .brand {
    position: absolute;
    top: 60px; left: 340px;
    display: flex; align-items: center; gap: 14px;
  }
  .brand-dot {
    width: 46px; height: 46px; border-radius: 50%;
    background: var(--gold);
  }
  .brand-name {
    color: var(--ink);
    font-size: 24px;
  }
  .headshot {
    position: absolute;
    top: 28px; left: 48px;
    width: 140px; height: 140px; border-radius: 50%;
    background: linear-gradient(160deg, var(--photo-a) 0%, var(--photo-a) 45%, var(--photo-b) 100%);
  }
  .person-name {
    position: absolute;
    top: 174px; left: 48px;
    font-family: "Montserrat", Arial, sans-serif;
    font-weight: 700; font-size: 30px; line-height: 36px;
    color: var(--gold);
  }
  .rule-long {
    position: absolute;
    top: 216px; left: 48px; width: 612px; height: 1.5px;
    background: var(--rule);
  }
  .person-title {
    position: absolute;
    top: 224px; left: 48px;
    font-size: 20px; line-height: 24px; color: var(--ink-soft);
  }
  .address {
    position: absolute;
    top: 226px; right: 40px;
    text-align: right;
    color: var(--ink-soft);
    font-size: 17px; line-height: 1.35;
  }
  .rule-short {
    position: absolute;
    top: 256px; left: 48px; width: 190px; height: 1.5px;
    background: var(--rule);
  }
  .contact {
    position: absolute;
    top: 264px; left: 48px;
    list-style: none;
    font-size: 20px; color: var(--ink);
  }
  .contact li { display: flex; align-items: center; gap: 12px; height: 30px; }
  .contact svg { width: 20px; height: 20px; }
  .band {
    position: absolute;
    left: 0; bottom: 22px; width: 100%; height: 34px;
    background: var(--gold);
    display: flex; align-items: center; justify-content: flex-end;
    padding-right: 60px;
  }
  .website { font-size: 20px; color: var(--ink); letter-spacing: 0.5px; }
</style>
</head>
<body>
  <section class="card card-back" aria-label="Card back">
    <span class="brand-dot"></span>
    <span class="brand-name">Marlowe Crest Realty, Inc</span>
  </section>

  <section class="card card-front" aria-label="Card front">
    <div class="headshot" role="img" aria-label="Portrait photo of the agent"></div>

    <div class="brand">
      <span class="brand-dot"></span>
      <span class="brand-name">Marlowe Crest Realty, Inc</span>
    </div>

    <h1 class="person-name">Gary Whitlock</h1>
    <div class="rule-long"></div>
    <p class="person-title">Broker/Owner</p>
    <p class="address">738 West Pinecrest Ave, Suite 410/510<br>Fort Lauderdale, FL 33308</p>
    <div class="rule-short"></div>

    <ul class="contact">
      <li>
        <svg viewBox="0 0 24 24" aria-hidden="true"><path fill="#f4c430" d="M6.6 10.8a15 15 0 0 0 6.6 6.6l2.2-2.2a1 1 0 0 1 1-.25 11.4 11.4 0 0 0 3.6.57 1 1 0 0 1 1 1V20a1 1 0 0 1-1 1A17 17 0 0 1 3 4a1 1 0 0 1 1-1h3.5a1 1 0 0 1 1 1c0 1.25.2 2.45.57 3.57a1 1 0 0 1-.25 1z"/></svg>
        <span>954-327-8846 Direct</span>
      </li>
      <li>
        <svg viewBox="0 0 24 24" aria-hidden="true"><rect x="2" y="5" width="20" height="14" rx="1" fill="#f4c430"/><path d="M2 6l10 7 10-7" fill="none" stroke="#fff" stroke-width="1.6"/></svg>
        <span>garyshomes@quellmail.com</span>
      </li>
    </ul>

    <div class="band"><span class="website">DwellTarrowBay.com</span></div>
  </section>
</body>
</html>
```